Business Card Design - Amberfield Court

We are looking at a new design for our business cards that has a modern and professional look. We run a residential aged care facility focussing on the care of residents. The cards will be used for potential clients, consultants and business opportunities in this sector. Blue and white is our main colours and would to see these colours incorporated in the design.
Industry/Entity Type
Business
Contact Information for Business Card
Amberfield Court, Darren Walsh, dwalsh@amberfieldcourt.com.au, Finance Manager, 0472 639 208, BCom, 37 Marrabel Crescent, Brindle Vale, Qld 4093.
Look and feel
Each slider illustrates characteristics of the customer's brand and the style your logo design should communicate.

```html
<!DOCTYPE html>
<html lang="en">
<head>
<meta charset="utf-8">
<title>Amberfield Court – Business Card</title>
<link href="https://fonts.googleapis.com/css2?family=Open+Sans:ital,wght@0,400;0,600;1,400&display=swap" rel="stylesheet">
<style>
  :root {
    --backdrop: #2e3034;
    --brand-blue: #4a7590;
    --brand-blue-deep: #43697f;
    --card-white: #e4e8ec;
    --ink: #1c1f24;
    --tag-taupe: #a89a8c;
    --white: #ffffff;
  }
  * { margin: 0; padding: 0; box-sizing: border-box; }
  html, body {
    width: 1200px; height: 864px; overflow: hidden;
    background: var(--backdrop);
    font-family: "Open Sans", Arial, sans-serif;
  }
  .canvas { position: relative; width: 1200px; height: 864px; }

  .card {
    position: absolute; left: 300px; width: 600px; height: 340px;
    border-radius: 3px;
  }

  /* Front */
  .card-front {
    top: 62px;
    background: var(--brand-blue-deep);
  }
  .front-wordmark {
    position: absolute; left: 0; right: 0; top: 168px;
    text-align: center; color: var(--white);
  }
  .front-wordmark .brand-name {
    font-size: 32px; font-weight: 400; letter-spacing: 4px;
    text-transform: uppercase; line-height: 1.2;
  }
  .front-wordmark .brand-tagline {
    display: inline-block; margin-top: 8px;
    font-size: 20px; font-style: italic; letter-spacing: 0.5px;
    background: var(--white); color: var(--brand-blue);
    padding: 1px 26px;
  }

  /* Back */
  .card-back {
    top: 462px;
    background: var(--card-white);
  }
  .back-brand {
    position: absolute; right: 40px; top: 46px;
    display: flex; align-items: center; gap: 12px;
  }
  .back-brand .brand-dot {
    width: 34px; height: 34px; border-radius: 50%;
    background: var(--brand-blue);
  }
  .back-brand .brand-name {
    font-size: 22px; letter-spacing: 2px; text-transform: uppercase;
    color: var(--brand-blue); font-weight: 400;
  }
  .back-tagline {
    position: absolute; right: 40px; top: 92px;
    font-size: 14px; font-style: italic; color: var(--white);
    background: var(--tag-taupe); padding: 1px 14px;
  }

  .holder { position: absolute; left: 44px; top: 150px; }
  .holder-name {
    font-size: 20px; font-weight: 600; color: var(--brand-blue);
  }
  .holder-name .credential { font-size: 14px; }
  .holder-role { font-size: 14px; color: var(--ink); margin-top: 2px; }

  .contact {
    position: absolute; right: 40px; bottom: 40px;
    text-align: right; font-size: 14px; color: var(--ink); line-height: 1.75;
  }
  .contact-line { display: flex; justify-content: flex-end; align-items: center; gap: 6px; }
  .contact-line svg { width: 13px; height: 13px; fill: var(--brand-blue); }
  .contact-address { padding-right: 19px; }
</style>
</head>
<body>
<main class="canvas">

  <section class="card card-front" aria-label="Business card front">
    <div class="front-wordmark">
      <div class="brand-name">Amberfield Court</div>
      <div class="brand-tagline">Comfort, Respect, Belonging</div>
    </div>
  </section>

  <section class="card card-back" aria-label="Business card back">
    <div class="back-brand">
      <span class="brand-dot"></span>
      <span class="brand-name">Amberfield Court</span>
    </div>
    <div class="back-tagline">Comfort, Respect, Belonging</div>

    <div class="holder">
      <div class="holder-name">Darren Walsh, <span class="credential">BCom</span></div>
      <div class="holder-role">Finance Manager</div>
    </div>

    <div class="contact">
      <div class="contact-line">
        <span>0472 639 208</span>
        <svg viewBox="0 0 24 24" aria-hidden="true"><path d="M6.6 10.8a15 15 0 0 0 6.6 6.6l2.2-2.2c.3-.3.7-.4 1-.2 1.1.4 2.3.6 3.6.6.6 0 1 .4 1 1V20c0 .6-.4 1-1 1A17 17 0 0 1 3 4c0-.6.4-1 1-1h3.5c.6 0 1 .4 1 1 0 1.3.2 2.5.6 3.6.1.3 0 .7-.2 1z"/></svg>
      </div>
      <div class="contact-line">
        <span>dwalsh@amberfieldcourt.com.au</span>
        <svg viewBox="0 0 24 24" aria-hidden="true"><path d="M2 5h20v14H2z M3.5 6.5 12 12.5l8.5-6z" fill-rule="evenodd"/></svg>
      </div>
      <div class="contact-address">37 Marrabel Crescent, Brindle Vale, Qld 4093</div>
    </div>
  </section>

</main>
</body>
</html>
```